Landscape design build company door flyer

I would like this flyer to convey a high-level of professionalism for a company that is excellent with communication with their clients as well as a company that does incredible installations

Went on vacation/holiday

```html
<!DOCTYPE html>
<html lang="en">
<head>
<meta charset="UTF-8">
<title>Cedarline Builders – Outdoor Living Spaces Flyer</title>
<link href="https://fonts.googleapis.com/css2?family=Montserrat:wght@400;500&family=Poppins:wght@500;600;700;800&display=swap" rel="stylesheet">
<style>
  :root{
    --navy:#0f2b40;
    --orange:#f26b0a;
    --paper:#e7e7e7;
    --stage:#dadada;
    --ink:#1c2228;
    --white:#ffffff;
  }
  *{box-sizing:border-box;margin:0;padding:0}
  html,body{width:1200px;height:1029px;overflow:hidden;background:var(--stage)}
  .flyer{
    position:absolute;left:212px;top:14px;width:777px;height:1000px;
    background:var(--paper);overflow:hidden;
    font-family:"Montserrat",sans-serif;color:var(--ink);
  }
  .brand{
    position:absolute;left:0;top:0;width:330px;height:169px;
    display:flex;flex-direction:column;align-items:center;justify-content:center;
  }
  .brand-mark{width:18px;height:18px;border-radius:50%;background:var(--orange);margin-bottom:10px}
  .brand-name{
    font-family:"Poppins",sans-serif;font-weight:600;font-size:21px;
    letter-spacing:.5px;color:var(--orange);line-height:1;
  }
  .brand-tagline{
    font-family:"Poppins",sans-serif;font-weight:500;font-size:9.5px;
    color:var(--navy);letter-spacing:.3px;margin-top:5px;
  }
  .hero-photo{
    position:absolute;left:0;top:0;width:777px;height:544px;
    clip-path:polygon(406px 0,100% 0,100% 100%,0 100%,0 169px,321px 169px);
    background:
      linear-gradient(180deg,rgba(0,0,0,0) 70%,#3f7a2c 82%,#4d8a33 100%),
      linear-gradient(100deg,#8a9aa3 0%,#9aa8ae 35%,#a88266 52%,#7f8f95 62%,#2f4a2e 78%,#213a22 100%);
  }
  .gallery-photo{
    position:absolute;top:418px;width:204px;height:204px;border-radius:50%;
    border:4px solid var(--white);
  }
  .gallery-photo.pergola{left:46px;background:linear-gradient(160deg,#c9b79a 0%,#a06c3c 40%,#5b5f66 75%,#3c4247 100%)}
  .gallery-photo.balcony{left:288px;background:linear-gradient(170deg,#b9c3c8 0%,#8e979b 45%,#7a8084 100%)}
  .gallery-photo.steps{left:527px;background:linear-gradient(170deg,#8b8b86 0%,#9b7656 40%,#7c5a3e 65%,#c3ad8f 100%)}
  .section-title{
    position:absolute;font-family:"Poppins",sans-serif;font-weight:700;
    font-size:26px;color:var(--navy);line-height:1;letter-spacing:-.2px;
  }
  .section-title::after{
    content:"";position:absolute;left:0;top:33px;width:70px;height:3px;
    border-radius:2px;background:var(--orange);
  }
  .about-title{left:38px;top:652px}
  .services-title{left:459px;top:652px}
  .about-text{
    position:absolute;left:38px;top:702px;width:352px;
    font-size:13.6px;line-height:15.85px;text-align:justify;color:var(--ink);
  }
  .service-list{position:absolute;left:463px;top:700px;list-style:none}
  .service-list li{
    display:flex;align-items:center;height:22.5px;
    font-family:"Poppins",sans-serif;font-weight:500;font-size:14.8px;color:var(--navy);
  }
  .service-list svg{width:13px;height:13px;margin-right:12px;flex:none}
  .footer-band{position:absolute;left:0;top:901px;width:777px;height:99px}
  .phone-icon{position:absolute;left:37px;top:926px;width:51px;height:51px;background:var(--orange);display:flex;align-items:center;justify-content:center}
  .phone-number{
    position:absolute;left:99px;top:922px;font-family:"Poppins",sans-serif;
    font-weight:700;font-size:45px;line-height:58px;color:var(--white);letter-spacing:-.5px;
  }
  .contact-list{position:absolute;left:518px;top:921px;list-style:none}
  .contact-list li{display:flex;align-items:center;height:25px;color:var(--white);font-family:"Poppins",sans-serif;font-weight:500;font-size:14.5px}
  .contact-list svg{width:17px;height:17px;margin-right:12px;flex:none}
</style>
</head>
<body>
<main class="flyer">
  <div class="hero-photo" role="img" aria-label="Photo of a two-level backyard deck with cedar railings and stairs beside a grey house, lawn and evergreen trees"></div>

  <header class="brand">
    <span class="brand-mark"></span>
    <span class="brand-name">CEDARLINE BUILDERS</span>
    <span class="brand-tagline">OUTDOOR LIVING SPACES</span>
  </header>

  <div class="gallery-photo pergola" role="img" aria-label="Photo of a timber pergola over a stone outdoor kitchen and paver patio"></div>
  <div class="gallery-photo balcony" role="img" aria-label="Photo of a grey composite balcony deck with black metal railing"></div>
  <div class="gallery-photo steps" role="img" aria-label="Photo of a brown composite deck with wraparound steps"></div>

  <h2 class="section-title about-title">ABOUT US</h2>
  <p class="about-text">Discover the endless possibilities for your outdoor space with The Cedarline Builders Team. Our team of skilled artisans is dedicated to turning your outdoor space into a breathtaking oasis that you’ll love coming home to. Whether it’s a cozy patio for intimate gatherings, a sprawling deck to host memorable parties, or a custom paver driveway that adds instant curb appeal, our high-quality craftsmanship ensures stunning results that exceed your expectations.</p>

  <h2 class="section-title services-title">OUR SERVICES</h2>
  <ul class="service-list">
    <li><svg viewBox="0 0 16 16"><circle cx="8" cy="8" r="8" fill="#f26b0a"/><path d="M4.5 8.3l2.3 2.2 4.7-4.8" fill="none" stroke="#fff" stroke-width="2" stroke-linecap="round" stroke-linejoin="round"/></svg>Paver Patios</li>
    <li><svg viewBox="0 0 16 16"><circle cx="8" cy="8" r="8" fill="#f26b0a"/><path d="M4.5 8.3l2.3 2.2 4.7-4.8" fill="none" stroke="#fff" stroke-width="2" stroke-linecap="round" stroke-linejoin="round"/></svg>Paver Driveways</li>
    <li><svg viewBox="0 0 16 16"><circle cx="8" cy="8" r="8" fill="#f26b0a"/><path d="M4.5 8.3l2.3 2.2 4.7-4.8" fill="none" stroke="#fff" stroke-width="2" stroke-linecap="round" stroke-linejoin="round"/></svg>Retaining Walls</li>
    <li><svg viewBox="0 0 16 16"><circle cx="8" cy="8" r="8" fill="#f26b0a"/><path d="M4.5 8.3l2.3 2.2 4.7-4.8" fill="none" stroke="#fff" stroke-width="2" stroke-linecap="round" stroke-linejoin="round"/></svg>Decks &amp; Railings</li>
    <li><svg viewBox="0 0 16 16"><circle cx="8" cy="8" r="8" fill="#f26b0a"/><path d="M4.5 8.3l2.3 2.2 4.7-4.8" fill="none" stroke="#fff" stroke-width="2" stroke-linecap="round" stroke-linejoin="round"/></svg>Pools</li>
    <li><svg viewBox="0 0 16 16"><circle cx="8" cy="8" r="8" fill="#f26b0a"/><path d="M4.5 8.3l2.3 2.2 4.7-4.8" fill="none" stroke="#fff" stroke-width="2" stroke-linecap="round" stroke-linejoin="round"/></svg>Outdoor Lighting</li>
    <li><svg viewBox="0 0 16 16"><circle cx="8" cy="8" r="8" fill="#f26b0a"/><path d="M4.5 8.3l2.3 2.2 4.7-4.8" fill="none" stroke="#fff" stroke-width="2" stroke-linecap="round" stroke-linejoin="round"/></svg>Firepits &amp; Fireplaces</li>
  </ul>

  <svg class="footer-band" viewBox="0 0 777 99" preserveAspectRatio="none" aria-hidden="true">
    <rect x="0" y="7" width="777" height="92" fill="var(--navy)"/>
    <polygon points="473,0 777,0 777,99 432,99" fill="var(--orange)"/>
  </svg>

  <div class="phone-icon">
    <svg width="28" height="28" viewBox="0 0 24 24" aria-hidden="true"><path d="M6.6 10.8a15.1 15.1 0 0 0 6.6 6.6l2.2-2.2a1 1 0 0 1 1-.25 11.4 11.4 0 0 0 3.6.57 1 1 0 0 1 1 1V20a1 1 0 0 1-1 1A17 17 0 0 1 3 4a1 1 0 0 1 1-1h3.5a1 1 0 0 1 1 1c0 1.25.2 2.45.57 3.57a1 1 0 0 1-.25 1z" fill="#fff"/></svg>
  </div>
  <div class="phone-number">206-555-0148</div>

  <ul class="contact-list">
    <li><svg viewBox="0 0 20 16" aria-hidden="true"><rect x="1" y="2" width="18" height="12" rx="1" fill="#fff"/><path d="M1.5 2.8L10 9l8.5-6.2" fill="none" stroke="#f26b0a" stroke-width="1.6"/></svg>info@cedarlinebuilders.com</li>
    <li><svg viewBox="0 0 20 20" aria-hidden="true" fill="none" stroke="#fff" stroke-width="1.4"><circle cx="10" cy="10" r="8"/><ellipse cx="10" cy="10" rx="3.5" ry="8"/><path d="M2 10h16M3.5 6h13M3.5 14h13"/></svg>www.cedarlinebuilders.com</li>
  </ul>
</main>
</body>
</html>
```